PWNF Traditional Business Card Project

Please see attached....just a simple business card... on attachment- please use the exact font, style, etc as the attached "Ned Farley Broughton" card... however, replace with the "Walter Augustin Pryde" text and address below the card.

```html
<!DOCTYPE html>
<html lang="en">
<head>
<meta charset="utf-8">
<title>PWNF Business Card</title>
<link href="https://fonts.googleapis.com/css2?family=Tinos:wght@400;700&display=swap" rel="stylesheet">
<style>
  :root {
    --backdrop: #e4e5e7;
    --card: #ffffff;
    --ink: #2f3949;
    --ink-soft: #3a3f47;
  }
  * { margin: 0; padding: 0; box-sizing: border-box; }
  html, body {
    width: 1200px; height: 900px; overflow: hidden;
    background: var(--backdrop);
  }
  .canvas {
    position: relative; width: 1200px; height: 900px;
    display: flex; align-items: center; justify-content: center;
  }
  .card {
    position: relative;
    width: 1000px; height: 572px;
    background: var(--card);
    box-shadow: 0 12px 30px rgba(0,0,0,0.18);
    font-family: "Tinos", "Times New Roman", serif;
    color: var(--ink);
  }
  .firm {
    position: absolute; left: 64px; top: 70px;
  }
  .firm-name {
    font-weight: 700; font-size: 50px; font-variant: small-caps;
    letter-spacing: 1px; line-height: 1;
  }
  .firm-sub {
    font-size: 19px; letter-spacing: 11px; text-transform: uppercase;
    color: var(--ink-soft); margin-top: 4px; padding-left: 4px;
  }
  .attorney {
    position: absolute; left: 0; right: 0; top: 250px;
    text-align: center;
  }
  .attorney-name {
    display: inline-block; text-align: right;
  }
  .attorney-name .name {
    font-weight: 700; font-size: 46px; font-variant: small-caps;
    letter-spacing: 1px; line-height: 1;
  }
  .attorney-name .title {
    font-size: 17px; text-transform: uppercase; letter-spacing: 1px;
    color: var(--ink-soft); margin-top: 4px; padding-right: 70px;
  }
  .address {
    position: absolute; right: 62px; top: 372px;
    text-align: right; font-size: 21px; line-height: 1.65;
    text-transform: uppercase; letter-spacing: 0.5px; color: var(--ink-soft);
  }
  .contact {
    position: absolute; left: 64px; bottom: 52px;
    list-style: none; font-size: 21px; color: var(--ink-soft);
  }
  .contact li {
    display: flex; align-items: center; gap: 16px; line-height: 1.55;
  }
  .contact svg { width: 20px; height: 20px; fill: var(--ink-soft); flex: none; }
</style>
</head>
<body>
<div class="canvas">
  <section class="card">
    <header class="firm">
      <div class="firm-name">Pacific Westbrook</div>
      <div class="firm-sub">Northgate Firm, PLC</div>
    </header>

    <div class="attorney">
      <div class="attorney-name">
        <div class="name">Ned Farley Broughton</div>
        <div class="title">Attorney at Law</div>
      </div>
    </div>

    <address class="address">
      4870 Harbor Ridge Road, Suite 210<br>
      Alder Springs, California 92700
    </address>

    <ul class="contact">
      <li>
        <svg viewBox="0 0 24 24" aria-hidden="true"><path d="M6.6 10.8a15.1 15.1 0 0 0 6.6 6.6l2.2-2.2c.3-.3.7-.4 1-.2 1.1.4 2.3.6 3.6.6.6 0 1 .4 1 1V20c0 .6-.4 1-1 1A17 17 0 0 1 3 4c0-.6.4-1 1-1h3.5c.6 0 1 .4 1 1 0 1.3.2 2.5.6 3.6.1.3 0 .7-.2 1z"/></svg>
        (555) 014-2231
      </li>
      <li>
        <svg viewBox="0 0 24 24" aria-hidden="true"><path d="M7 3h10v4H7zM4 8h16a2 2 0 0 1 2 2v6h-4v5H6v-5H2v-6a2 2 0 0 1 2-2zm4 7v4h8v-4z"/></svg>
        (555) 014-2232
      </li>
      <li>
        <svg viewBox="0 0 24 24" aria-hidden="true"><path d="M2 5h20v14H2zm2 2v.5l8 5.5 8-5.5V7zm0 2.9V17h16V9.9l-8 5.5z"/></svg>
        nbroughton@broughtonpryde.com
      </li>
      <li>
        <svg viewBox="0 0 24 24" aria-hidden="true"><path d="M12 2a10 10 0 1 0 0 20 10 10 0 0 0 0-20zm6.9 6h-3a15 15 0 0 0-1.3-4A8 8 0 0 1 18.9 8zM12 4c.9 1.2 1.6 2.6 2 4h-4c.4-1.4 1.1-2.8 2-4zM4.3 14a8 8 0 0 1 0-4h3.4a16 16 0 0 0 0 4zm.8 2h3a15 15 0 0 0 1.3 4A8 8 0 0 1 5.1 16zm3-8h-3a8 8 0 0 1 4.3-4A15 15 0 0 0 8.1 8zM12 20c-.9-1.2-1.6-2.6-2-4h4c-.4 1.4-1.1 2.8-2 4zm2.3-6H9.7a14 14 0 0 1 0-4h4.6a14 14 0 0 1 0 4zm.3 6a15 15 0 0 0 1.3-4h3a8 8 0 0 1-4.3 4zm1.7-6a16 16 0 0 0 0-4h3.4a8 8 0 0 1 0 4z"/></svg>
        www.broughtonpryde.com
      </li>
    </ul>
  </section>
</div>
</body>
</html>
```